design a construction company business card

Design business card around our logo. Card must have all the typical info: name, title, address, phone, email, business name, etc. Somewhere on the card I would like to see our motto "Built on integrity... Inspired by commitment." Consider adding a splash of bright orange to the card to complement the blues and silvers/grays in the logo. We are open to metallic inks, textures, etc. We would like to see options on both light and dark backgrounds. The font in the logo is Euro Technic Extended Regular.

```html
<!DOCTYPE html>
<html lang="en">
<head>
<meta charset="utf-8">
<title>Halden Contracting – Business Card</title>
<link rel="stylesheet" href="https://fonts.googleapis.com/css2?family=Roboto:ital,wght@0,300;0,400;0,500;0,700;1,400&display=swap">
<style>
  :root {
    --page-bg: #d8d5d1;
    --card-bg: #eeedeb;
    --brand-orange: #d4502a;
    --name-red: #c42f1c;
    --band-orange-start: #e0582a;
    --band-orange-end: #c02a18;
    --band-dark: #3b3c40;
    --text-dark: #3e3f43;
    --text-light: #fbe9df;
  }
  * { box-sizing: border-box; margin: 0; padding: 0; }
  html, body {
    width: 1200px;
    height: 969px;
    overflow: hidden;
    background: var(--page-bg);
    font-family: "Roboto", Arial, sans-serif;
  }
  .business-card {
    position: absolute;
    left: 100px;
    top: 199px;
    width: 1000px;
    height: 571px;
    background: var(--card-bg);
    overflow: hidden;
    box-shadow: 0 10px 30px rgba(0,0,0,0.18);
  }
  .company-name {
    position: absolute;
    left: 68px;
    top: 74px;
    font-size: 62px;
    font-weight: 700;
    letter-spacing: 4px;
    line-height: 1;
    color: var(--brand-orange);
  }
  .company-suffix {
    position: absolute;
    left: 68px;
    top: 148px;
    font-size: 23px;
    font-weight: 400;
    letter-spacing: 0.5px;
    color: var(--text-dark);
  }
  .person {
    position: absolute;
    right: 75px;
    top: 90px;
    text-align: right;
  }
  .person-name {
    font-size: 40px;
    font-weight: 700;
    color: var(--name-red);
    line-height: 1.05;
    letter-spacing: 0.5px;
  }
  .person-title {
    font-size: 25px;
    font-weight: 400;
    color: var(--text-dark);
    margin-top: 6px;
    letter-spacing: 0.5px;
  }
  .info-band {
    position: absolute;
    left: 0;
    top: 249px;
    width: 745px;
    height: 258px;
    background: linear-gradient(90deg, var(--band-orange-start), var(--band-orange-end));
  }
  .dark-band {
    position: absolute;
    left: 745px;
    top: 249px;
    width: 255px;
    height: 258px;
    background: var(--band-dark);
  }
  .skyline-art {
    position: absolute;
    left: 615px;
    top: 249px;
    width: 385px;
    height: 258px;
  }
  .address {
    position: absolute;
    left: 71px;
    top: 292px;
    font-size: 22px;
    font-weight: 300;
    line-height: 30px;
    color: var(--text-light);
  }
  .contact-list {
    position: absolute;
    left: 71px;
    top: 370px;
    list-style: none;
    font-size: 22px;
    font-weight: 300;
    color: var(--text-light);
  }
  .contact-list li {
    display: flex;
    align-items: center;
    height: 32px;
  }
  .contact-list svg {
    width: 20px;
    height: 20px;
    margin-right: 12px;
    fill: var(--text-light);
  }
  .motto {
    position: absolute;
    left: 71px;
    top: 521px;
    font-size: 23px;
    font-style: italic;
    font-weight: 400;
    color: var(--text-dark);
  }
</style>
</head>
<body>
  <div class="business-card">
    <div class="company-name">HALDEN</div>
    <div class="company-suffix">— CONTRACTING, INC. —</div>

    <div class="person">
      <div class="person-name">MARK ELLISON</div>
      <div class="person-title">CEO/FOUNDER</div>
    </div>

    <div class="info-band"></div>
    <div class="dark-band"></div>
    <svg class="skyline-art" role="img" aria-label="Illustration of a city skyline of tall buildings" viewBox="0 0 385 258">
      <defs>
        <linearGradient id="skylineTone" x1="0" x2="1" y1="0" y2="0">
          <stop offset="0" stop-color="#c42a18" stop-opacity="0"/>
          <stop offset="0.35" stop-color="#a8251a"/>
          <stop offset="0.34" stop-color="#a8251a"/>
          <stop offset="0.36" stop-color="#2e2f33"/>
          <stop offset="1" stop-color="#2e2f33" stop-opacity="0.6"/>
        </linearGradient>
      </defs>
      <rect x="0" y="0" width="385" height="258" fill="url(#skylineTone)" opacity="0.45"/>
    </svg>

    <div class="address">
      4210 Alder Ridge Road<br>
      Anchorage, Alaska 34581
    </div>

    <ul class="contact-list">
      <li>
        <svg viewBox="0 0 24 24" aria-hidden="true"><path d="M6.6 10.8a15.1 15.1 0 0 0 6.6 6.6l2.2-2.2a1 1 0 0 1 1-.25 11.4 11.4 0 0 0 3.6.57 1 1 0 0 1 1 1V20a1 1 0 0 1-1 1A17 17 0 0 1 3 4a1 1 0 0 1 1-1h3.5a1 1 0 0 1 1 1c0 1.25.2 2.45.57 3.57a1 1 0 0 1-.25 1z"/></svg>
        689 555 0147
      </li>
      <li>
        <svg viewBox="0 0 24 24" aria-hidden="true"><path d="M2 5h20v14H2z" opacity="0.9"/><path d="M2 5l10 8 10-8" fill="none" stroke="#c94020" stroke-width="1.8"/></svg>
        mark@halden.com
      </li>
      <li>
        <svg viewBox="0 0 24 24" aria-hidden="true"><circle cx="12" cy="12" r="10"/><path d="M2 12h20M12 2c3 3 3 17 0 20M12 2c-3 3-3 17 0 20" fill="none" stroke="#c94020" stroke-width="1.4"/></svg>
        www.halden.com
      </li>
    </ul>

    <div class="motto">Built on integrity... Inspired by commitment.</div>
  </div>
</body>
</html>
```